Industry automation wholesale website

www.velturo.eu provides solutions for automation, building automation and digital signage.

Our products are rugged, reliable, energy saving and representative.

Scope of pages:
● welcome page
- scope of products
- applications, success stories and news
● category page
- short introduction
- sub categories
- product highlights
● product page
- short introduction
- about 3 to 4 pictures
- technical specifications: materials, dimensions
- price
- related products

Optional:
● contact page
- address
- contact form
● blog
- picture
- text
● logo
● favicon / apple touch icon

Conclusion:
● We need a professionally looking site
● Bright colors (e.g. white, grey, metalic colors, blue)

some pages we like:
http://www.prandek.de/
http://www.morvalix.de/

Target Market(s)

Our target market is the industrial sector
● Target audience: engineering and IT professionals

Industry/Entity Type

Building

Requirements
Must have
• ● only use free available fonts e.g. Lumara Type Library (http://www.lumaratype.com/webfonts)
Should not have
• ● sound
● flash

```html
<!DOCTYPE html>
<html lang="en">
<head>
<meta charset="utf-8">
<title>velturo – analog digital measurements</title>
<link href="https://fonts.googleapis.com/css2?family=Open+Sans:wght@400;600;700&display=swap" rel="stylesheet">
<style>
:root{
  --blue:#1b78ad;
  --blue-dark:#155f8a;
  --title-blue:#1a6b9a;
  --link-blue:#1e7ab8;
  --text:#333;
  --muted:#555;
  --rule:#ddd;
  --page-bg:#ececec;
  --bar:#6a6a6a;
  --bar-dark:#454545;
  --head-top:#7b7b7b;
  --head-bottom:#575757;
  --red:#e21b1b;
}
*{box-sizing:border-box;margin:0;padding:0}
html,body{width:1128px;height:1200px;overflow:hidden}
body{background:var(--page-bg);font-family:"Open Sans",Arial,sans-serif;color:var(--text);position:relative}
.abs{position:absolute}
.page{position:absolute;left:104px;top:0;width:920px;height:1059px;background:#fff;box-shadow:0 0 4px rgba(0,0,0,.12)}
.topbar{position:absolute;left:104px;top:0;width:920px;height:22px;background:var(--bar);color:#fff;font-size:12px;font-weight:700}
.topbar .contact{position:absolute;top:3px;display:flex;align-items:center;gap:5px}
.topbar .lang{position:absolute;right:0;top:0;width:95px;height:22px;background:var(--bar-dark);font-weight:400;font-size:11px;display:flex;align-items:center;justify-content:center;gap:6px}
.flag{width:16px;height:10px;background:#2b4a8f;border:1px solid #fff}
.logo{left:122px;top:38px}
.logo .name{font-size:52px;font-weight:400;color:var(--blue);letter-spacing:1px;line-height:1}
.logo .tag{font-size:12px;color:var(--blue);margin-top:2px}
.cart{left:647px;top:46px;font-size:12px;display:flex;align-items:center;gap:5px}
.search{left:827px;top:41px;width:179px;height:24px;border:1px solid #ccc;border-radius:3px;font-size:11px;color:#999;padding:3px 10px}
.nav{left:637px;top:80px;display:flex;gap:0;font-size:13px}
.nav a{color:#222;text-decoration:none;padding:3px 10px;margin-right:3px}
.nav a.active{background:var(--blue);color:#fff;border-radius:2px}
.slider{left:122px;top:120px;width:885px;height:330px}
.slide-title{left:607px;top:181px;font-size:25px;font-weight:700;color:var(--title-blue)}
.feature{left:608px;font-size:15px;line-height:20px}
.feature b{font-weight:700;display:block}
.btn-big{left:609px;top:381px;width:120px;height:35px;background:var(--blue);color:#fff;font-size:14px;display:flex;align-items:center;justify-content:center;border-radius:3px;border-bottom:3px solid var(--blue-dark)}
.box{top:474px;width:207px;height:287px;border:1px solid #ddd;background:#fff;box-shadow:0 1px 2px rgba(0,0,0,.1)}
.box h2{height:32px;background:linear-gradient(var(--head-top),var(--head-bottom));color:#fff;font-size:14px;font-weight:600;padding:7px 15px;text-transform:uppercase}
.range{list-style:none;padding:0 16px}
.range li{height:27px;border-bottom:1px solid #e5e5e5;font-size:11.5px;display:flex;align-items:center;justify-content:space-between}
.range li:last-child{border:none}
.plus{width:10px;height:10px;border:1px solid #bbb;font-size:9px;line-height:8px;text-align:center;color:#999}
.photo{margin:12px 13px 0;width:180px;height:135px}
.box p{font-size:11.5px;line-height:20px;margin:8px 13px 0;color:#333}
.btn{display:inline-block;background:var(--blue);color:#fff;font-size:10px;font-weight:700;border-radius:3px;padding:3px 12px;margin:7px 14px 0}
.sec-title{font-size:14px;font-weight:600;color:#222;text-transform:uppercase}
.item{height:64px;border-bottom:1px solid var(--rule);display:flex;gap:10px;padding-top:2px}
.item:last-of-type{border:none}
.date{width:43px;flex:none}
.date .m{height:22px;background:#ddd;font-size:11px;text-align:center;line-height:22px}
.date .d{height:22px;background:var(--blue);color:#fff;font-weight:700;font-size:14px;text-align:center;line-height:22px}
.thumb{width:61px;height:45px;flex:none;background:linear-gradient(#9fc6e2,#d9e9f3)}
.item h3{font-size:12px;font-weight:600;color:var(--link-blue);line-height:16px}
.item p{font-size:10.5px;line-height:18px;color:#333}
.footer{left:0;width:1128px;text-align:center;font-size:11.5px;color:#444}
.social{left:513px;top:1154px;display:flex;gap:7px}
.social span{width:30px;height:30px;border-radius:50%}
</style>
</head>
<body>
<div class="page"></div>

<div class="topbar">
  <div class="contact" style="left:555px">
    <svg width="15" height="15" viewBox="0 0 16 16"><circle cx="8" cy="8" r="7" fill="none" stroke="#fff" stroke-width="1.2"/><rect x="4" y="5.5" width="8" height="5.5" fill="none" stroke="#fff"/><path d="M4 5.5 8 8.5 12 5.5" fill="none" stroke="#fff"/></svg>
    info@velturo.de
  </div>
  <div class="contact" style="left:688px">
    <svg width="15" height="15" viewBox="0 0 16 16"><circle cx="8" cy="8" r="7" fill="none" stroke="#fff" stroke-width="1.2"/><path d="M5.5 4.5c-.8.8-.5 2.6 1.5 4.7 2 2 3.8 2.3 4.6 1.5l-1.3-1.3-1 .6c-.7-.3-1.7-1.3-2-2l.6-1z" fill="#fff"/></svg>
    +49-211-5550142
  </div>
  <div class="lang">Language <span class="flag"></span></div>
</div>

<div class="abs logo">
  <div class="name">velturo</div>
  <div class="tag">analog digital measurements</div>
</div>

<div class="abs cart">
  <svg width="14" height="12" viewBox="0 0 14 12"><path d="M0 1h2.5l2 7h7l1.5-5H4" fill="none" stroke="var(--blue)" stroke-width="1.5"/><circle cx="5.5" cy="10.5" r="1.2" fill="var(--blue)"/><circle cx="10.5" cy="10.5" r="1.2" fill="var(--blue)"/></svg>
  Products:0 Price: $0.00
</div>
<div class="abs search">Product search
  <svg class="abs" style="right:7px;top:5px" width="13" height="13" viewBox="0 0 13 13"><circle cx="5.5" cy="5.5" r="4.5" fill="none" stroke="#999" stroke-width="1.4"/><path d="M9 9l3.5 3.5" stroke="#999" stroke-width="1.6"/></svg>
</div>

<nav class="abs nav">
  <a class="active">HOME</a><a>ABOUT US</a><a>PRODUCTS</a><a>BLOG</a><a>CONTACT US</a>
</nav>

<svg class="abs slider" viewBox="0 0 885 330">
  <defs>
    <linearGradient id="sky" x1="0" y1="0" x2="1" y2="1">
      <stop offset="0" stop-color="#d3ebf7"/><stop offset=".45" stop-color="#6fb8e2"/><stop offset="1" stop-color="#c2e2f3"/>
    </linearGradient>
    <linearGradient id="screen" x1="0" y1="0" x2="1" y2="1">
      <stop offset="0" stop-color="#3a3a3a"/><stop offset="1" stop-color="#1d4fa0"/>
    </linearGradient>
  </defs>
  <path d="M0 18 Q442 -18 885 18 V300 Q442 350 0 300Z" fill="url(#sky)"/>
  <path d="M470 0 Q560 80 520 200 Q490 290 600 330 H885 V0Z" fill="#fff" opacity=".12"/>
  <rect x="86" y="24" width="234" height="276" fill="url(#screen)" role="img" aria-label="Touch panel PC product photo"/>
  <circle cx="84" cy="114" r="38" fill="var(--red)"/>
  <text x="84" y="121" text-anchor="middle" font-family="Open Sans,Arial,sans-serif" font-size="21" font-weight="700" fill="#fff">NEW</text>
  <g fill="none" stroke="#fff" stroke-width="2">
    <circle cx="33" cy="166" r="14"/><path d="M36 159l-7 7 7 7"/>
    <circle cx="854" cy="166" r="14"/><path d="M851 159l7 7-7 7"/>
  </g>
</svg>

<div class="abs slide-title">Touch Panel PC/Bedienterminal</div>
<div class="abs feature" style="top:229px"><b>Industrial</b>IP65 Front 24/7 continous operation</div>
<div class="abs feature" style="top:277px"><b>Performance</b>Corvex Dual Core C525 1,8 GHz</div>
<div class="abs feature" style="top:325px"><b>Fanless</b>Low heat emission, power saving</div>
<div class="abs btn-big">View Details</div>

<section class="abs box" style="left:122px">
  <h2>Range of Products</h2>
  <ul class="range">
    <li>RS422 / RS485 Converter<span class="plus">+</span></li>
    <li>RS422 / RS485 Repeater<span class="plus">+</span></li>
    <li>Embedded Systems<span class="plus">+</span></li>
    <li>RS485 Remote IO<span class="plus">+</span></li>
    <li>RS485 Modbus IO<span class="plus">+</span></li>
    <li>Embedded Systems<span class="plus">+</span></li>
    <li>PCI-Series<span class="plus">+</span></li>
    <li>Industry PC<span class="plus">+</span></li>
    <li>Industrial Display<span class="plus">+</span></li>
  </ul>
</section>
<section class="abs box" style="left:347px">
  <h2>Modbus RTU / RS485</h2>
  <div class="photo" role="img" aria-label="Row of RS485 remote IO modules" style="background:linear-gradient(135deg,#8fb8de,#3f7fc0)"></div>
  <p>RS485 Remote IO modules are ideal to realize decentralized distributed IO units over long distances.</p>
  <span class="btn">View Details</span>
</section>
<section class="abs box" style="left:574px">
  <h2>Touch Panel Industry</h2>
  <div class="photo" role="img" aria-label="Industrial touch panel display" style="background:linear-gradient(135deg,#b9c3cc,#6f9fd0)"></div>
  <p>RS485 Remote IO modules are ideal to realize decentralized distributed IO units over long distances.</p>
  <span class="btn">View Details</span>
</section>
<section class="abs box" style="left:800px">
  <h2>Embedded Systems</h2>
  <div class="photo" role="img" aria-label="Embedded industrial PC box" style="background:linear-gradient(135deg,#a6c8e8,#5d8fc4)"></div>
  <p>RS485 Remote IO modules are ideal to realize decentralized distributed IO units over long distances.</p>
  <span class="btn">View Details</span>
</section>

<section class="abs" style="left:122px;top:783px;width:446px">
  <h2 class="sec-title" style="margin-bottom:7px">Latest News</h2>
  <div class="item"><div class="date"><div class="m">Jan</div><div class="d">03</div></div><div><h3>Lorem Ipsum is simply</h3><p>Lorem Ipsum is simply dummy text of the printing and typesetting industry. Lorem Ipsum has been the industry</p></div></div>
  <div class="item"><div class="date"><div class="m">Jan</div><div class="d">03</div></div><div><h3>Lorem Ipsum is simply</h3><p>Lorem Ipsum is simply dummy text of the printing and typesetting industry. Lorem Ipsum has been the industry</p></div></div>
  <div class="item"><div class="date"><div class="m">Jan</div><div class="d">03</div></div><div><h3>Lorem Ipsum is simply</h3><p>Lorem Ipsum is simply dummy text of the printing and typesetting industry. Lorem Ipsum has been the industry</p></div></div>
  <span class="btn" style="margin:0">View All News</span>
</section>

<section class="abs" style="left:606px;top:783px;width:390px">
  <h2 class="sec-title" style="margin-bottom:7px">Success Stories</h2>
  <div class="item"><div class="thumb" role="img" aria-label="Customer story photo"></div><div><h3>Lorem Ipsum is simply</h3><p>Lorem Ipsum is simply dummy text of the printing and typesetting industry. Lorem Ipsum has been the industry</p></div></div>
  <div class="item"><div class="thumb" role="img" aria-label="Customer story photo"></div><div><h3>Lorem Ipsum is simply</h3><p>Lorem Ipsum is simply dummy text of the printing and typesetting industry. Lorem Ipsum has been the industry</p></div></div>
  <div class="item"><div class="thumb" role="img" aria-label="Customer story photo"></div><div><h3>Lorem Ipsum is simply</h3><p>Lorem Ipsum is simply dummy text of the printing and typesetting industry. Lorem Ipsum has been the industry</p></div></div>
  <span class="btn" style="margin:0;padding:3px 20px">View All</span>
</section>

<div class="abs footer" style="top:1079px">Home &nbsp;|&nbsp; About Us &nbsp;|&nbsp; Products &nbsp;|&nbsp; Blog &nbsp;|&nbsp; Contact Us</div>
<div class="abs footer" style="top:1102px">Copyright © 2014 velturo.eu. All Rights Reserved.</div>
<div class="abs footer" style="top:1126px;font-size:10.5px">Terms &amp; Conditions &nbsp;|&nbsp; Masthead</div>
<div class="abs social">
  <span role="img" aria-label="Social network link" style="background:#3b5a98"></span>
  <span role="img" aria-label="Social network link" style="background:#2a9fd8"></span>
  <span role="img" aria-label="Social network link" style="background:#d03a2f"></span>
</div>
</body>
</html>
```